New Dental Office Needs an Attractive and user friendly Website Designed

I need a website for a new dental office. The Name is Harrowfield Dentistry. I would like a Modern design with a user friendly interface and usability.
I would like a landing page, a page that lists the services we offer: Cosmetic Dentistry, Implants, Dental Hygiene, Emergency Services, Restorations, Dentures
Target Market(s)
Mid to upper class
Industry/Entity Type
Dentistry
Coding
Number of Pages Required
1 page
Requirements
Must have
- Landing page that has a scheduling option, Procedures, operating hours, and contact us info
Nice to have
- Appealing design, Soft comforting colors. Easy to navigate page, Modern and professional.

```html
<!DOCTYPE html>
<html lang="en">
<head>
<meta charset="UTF-8">
<title>Harrowfield Dentistry</title>
<link href="https://fonts.googleapis.com/css2?family=Playfair+Display:wght@500;600;700&family=Lato:wght@400;700&family=Montserrat:wght@500;600&display=swap" rel="stylesheet">
<style>
:root{
  --navy:#2d3e50;
  --navy-dark:#25272a;
  --teal:#5dc2b6;
  --teal-soft:#e4f3f1;
  --blue:#1da1e2;
  --gold:#d9b13a;
  --ink:#1f2933;
  --muted:#5b6673;
  --page:#f5f7f9;
  --white:#ffffff;
}
*{margin:0;padding:0;box-sizing:border-box}
html,body{width:1200px;height:3450px;overflow:hidden}
body{position:relative;background:var(--page);font-family:'Lato',sans-serif;color:var(--ink)}

/* header */
.site-header{position:absolute;left:0;top:0;width:1200px;height:94px;background:var(--white)}
.brand{position:absolute;left:141px;top:28px;font-family:'Playfair Display',serif;font-weight:600;font-size:28px;color:var(--ink)}
.nav{position:absolute;top:40px;font-family:'Montserrat',sans-serif;font-weight:500;font-size:13px;color:var(--ink)}
.nav.active{color:var(--blue)}
.btn-book{position:absolute;display:flex;align-items:center;gap:8px;background:var(--blue);color:#fff;font-family:'Montserrat',sans-serif;font-weight:600;font-size:13px;border-radius:22px;padding:0 22px}
.btn-book svg{width:16px;height:16px}

/* hero */
.hero{position:absolute;left:0;top:94px;width:1200px;height:531px;background:linear-gradient(110deg,#e7f4fa 0%,#cfeaf6 55%,#e4f3fa 100%);overflow:hidden}
.hero-photo{position:absolute;left:630px;top:0;width:570px;height:531px;background:radial-gradient(ellipse at 55% 40%,#e9c9b2 0%,#d9a98b 30%,#f1f1ef 62%,#dcecf4 100%)}
.hero-tooth{position:absolute;left:0;top:341px;width:174px;height:190px;background:radial-gradient(ellipse at 55% 55%,#ffffff 0%,#e6eef2 55%,rgba(220,236,244,0) 75%)}
.hero h1{position:absolute;left:141px;top:94px;width:500px;font-family:'Playfair Display',serif;font-weight:600;font-size:52px;line-height:64px;color:var(--ink)}
.hero-sub{position:absolute;left:139px;top:296px;width:470px;font-family:'Montserrat',sans-serif;font-weight:500;font-size:20px;line-height:32px;color:var(--ink)}
.chat-pill{position:absolute;left:825px;top:428px;width:234px;height:43px;background:#fff;border-radius:22px;display:flex;align-items:center;gap:8px;padding-left:20px;font-size:11px;line-height:13px;color:var(--ink)}
.chat-avatar{width:26px;height:26px;border-radius:50%;background:#b9a394;flex:none}
.chat-close{position:absolute;left:820px;top:422px;width:20px;height:20px;border-radius:50%;background:#111;color:#fff;font-size:11px;font-weight:700;display:flex;align-items:center;justify-content:center}
.chat-btn{position:absolute;left:1009px;top:419px;width:60px;height:60px;border-radius:50%;background:#1b4d9c;border:4px solid #4a7bd0;display:flex;align-items:center;justify-content:center}

/* section headings */
.sec-title{position:absolute;left:0;width:1200px;text-align:center;font-family:'Playfair Display',serif;font-weight:600;font-size:29px}
.sec-title span{border-bottom:3px solid var(--gold);padding-bottom:1px}
.sec-sub{position:absolute;text-align:center;font-size:12.5px;line-height:16px}

/* services */
.services{position:absolute;left:0;top:625px;width:1200px;height:624px;background:var(--page)}
.service-card{position:absolute;width:292px;height:187px;background:var(--teal-soft);border-radius:16px}
.svc-icon{position:absolute;left:21px;top:21px;width:42px;height:42px;border-radius:7px;background:var(--teal);display:flex;align-items:center;justify-content:center}
.svc-icon svg{width:26px;height:26px}
.service-card h3{position:absolute;left:21px;top:94px;font-family:'Playfair Display',serif;font-weight:600;font-size:19.5px;color:var(--navy)}
.service-card p{position:absolute;left:21px;top:121px;width:250px;font-size:12.5px;line-height:15.5px;color:var(--muted)}

/* why choose */
.why{position:absolute;left:0;top:1249px;width:1200px;height:694px;background:var(--navy);color:#fff}
.why-item{position:absolute;left:141px;width:423px;height:98px;background:var(--page);border-radius:9px}
.why-icon{position:absolute;left:14px;top:13px;width:72px;height:72px;border-radius:8px;background:#e6ecee;display:flex;align-items:center;justify-content:center}
.why-icon svg{width:38px;height:38px}
.why-item h3{position:absolute;left:99px;top:16px;font-family:'Playfair Display',serif;font-weight:600;font-size:20px;color:var(--navy)}
.why-item p{position:absolute;left:99px;top:46px;width:310px;font-size:12.5px;line-height:15.5px;color:#7a838d}
.why-frame{position:absolute;left:600px;top:177px;width:469px;height:447px;background:var(--teal);border-radius:90px 0 90px 0}
.why-photo{position:absolute;left:600px;top:188px;width:458px;height:436px;border-radius:90px 0 90px 0;background:linear-gradient(160deg,#d7dde1 0%,#b7c1c8 35%,#eceef0 70%,#c9d1d6 100%)}

/* visit */
.visit{position:absolute;left:0;top:1943px;width:1200px;height:719px;background:var(--page)}
.map{position:absolute;left:141px;top:186px;width:641px;height:462px;background:linear-gradient(135deg,#a9cdee 0%,#eef0e8 35%,#f3f1ea 60%,#a9cdee 100%)}
.info-card{position:absolute;left:758px;top:254px;width:300px;height:326px;background:var(--navy);border-radius:12px;color:#fff}
.info-card h4{position:absolute;left:28px;display:flex;align-items:center;gap:6px;font-family:'Playfair Display',serif;font-weight:600;font-size:19px}
.info-card h4 svg{width:18px;height:18px}
.info-card p{position:absolute;left:28px;font-size:12.5px;line-height:15.5px}
.btn-call{position:absolute;left:28px;top:265px;width:93px;height:31px;background:#fff;color:var(--ink);border-radius:4px;font-size:12.5px;display:flex;align-items:center;justify-content:center}

/* testimonials */
.reviews{position:absolute;left:0;top:2662px;width:1200px;height:509px;background:var(--navy);color:#fff}
.review-card{position:absolute;top:171px;width:448px;height:192px;background:var(--page);border-radius:10px;color:var(--ink)}
.stars{position:absolute;left:21px;top:22px;display:flex;gap:4px}
.stars svg{width:21px;height:21px}
.review-date{position:absolute;right:22px;top:26px;font-size:12.5px}
.review-text{position:absolute;left:21px;top:68px;width:412px;font-size:12.5px;line-height:15.5px}
.reviewer{position:absolute;left:21px;top:116px;display:flex;align-items:center;gap:14px}
.reviewer-avatar{width:56px;height:56px;border-radius:50%;background:#c9a98f}
.reviewer b{display:block;font-family:'Playfair Display',serif;font-weight:600;font-size:19px;color:var(--navy)}
.reviewer small{font-size:12px;color:#7a838d}
.arrow-btn{position:absolute;top:256px;width:28px;height:28px;border-radius:4px;display:flex;align-items:center;justify-content:center}
.btn-view{position:absolute;left:548px;top:407px;width:105px;height:38px;background:var(--teal);border-radius:4px;color:#fff;font-size:13px;display:flex;align-items:center;justify-content:center}

/* footer */
.site-footer{position:absolute;left:0;top:3171px;width:1200px;height:279px;background:var(--navy-dark);color:#fff}
.footer-brand{position:absolute;left:0;top:60px;width:1200px;text-align:center;font-family:'Playfair Display',serif;font-weight:600;font-size:24px}
.footer-links{position:absolute;left:0;top:127px;width:1200px;display:flex;justify-content:center;gap:28px;font-family:'Playfair Display',serif;font-size:13px}
.socials{position:absolute;left:0;top:165px;width:1200px;display:flex;justify-content:center;gap:28px}
.socials span{width:15px;height:15px;border-radius:3px;background:#fff}
.footer-rule{position:absolute;left:0;top:236px;width:1200px;height:1px;background:#3a3d42}
.copyright{position:absolute;left:0;top:251px;width:1200px;text-align:center;font-size:11px}
</style>
</head>
<body>

<header class="site-header">
  <div class="brand">Harrowfield Dentistry</div>
  <div class="nav active" style="left:509px">HOME</div>
  <div class="nav" style="left:593px">SERVICES</div>
  <div class="nav" style="left:699px">CONTACT US</div>
  <div class="btn-book" style="left:826px;top:28px;height:41px">
    <svg viewBox="0 0 16 16" fill="none" stroke="#fff" stroke-width="1.4"><rect x="2" y="3" width="12" height="11" rx="1"/><path d="M2 6.5h12M5 1.5v3M11 1.5v3M5 9h1M8 9h1M11 9h1M5 11.5h1M8 11.5h1"/></svg>
    BOOK AN APPOINTMENT
  </div>
</header>

<section class="hero">
  <div class="hero-photo" role="img" aria-label="Smiling woman touching her cheek, showing bright teeth"></div>
  <div class="hero-tooth" role="img" aria-label="White tooth model with dental mirror"></div>
  <h1>Premium Dental Care for a Confident Smile</h1>
  <p class="hero-sub">Expert Cosmetic And Restorative Dentistry<br>In A Luxurious Setting.</p>
  <div class="btn-book" style="left:141px;top:384px;height:42px">
    <svg viewBox="0 0 16 16" fill="none" stroke="#fff" stroke-width="1.4"><rect x="2" y="3" width="12" height="11" rx="1"/><path d="M2 6.5h12M5 1.5v3M11 1.5v3M5 9h1M8 9h1M11 9h1M5 11.5h1M8 11.5h1"/></svg>
    BOOK AN APPOINTMENT
  </div>
  <div class="chat-pill"><span class="chat-avatar" role="img" aria-label="Support agent avatar"></span><span>Lorem Ipsum Simply<br>Dummy Text.</span></div>
  <div class="chat-close">x</div>
  <div class="chat-btn">
    <svg width="30" height="30" viewBox="0 0 30 30"><path d="M15 5C8.4 5 4 9.2 4 14c0 2.7 1.4 5 3.7 6.6L6.5 25l4.8-2.6c1.2.3 2.4.5 3.7.5 6.6 0 11-4.2 11-9S21.6 5 15 5z" fill="#fff"/><circle cx="10.5" cy="14" r="1.6" fill="#1b4d9c"/><circle cx="15" cy="14" r="1.6" fill="#1b4d9c"/><circle cx="19.5" cy="14" r="1.6" fill="#1b4d9c"/></svg>
  </div>
</section>

<section class="services">
  <h2 class="sec-title" style="top:42px;color:var(--navy)">Our Dental <span>Services</span></h2>
  <p class="sec-sub" style="top:84px;left:400px;width:400px;color:var(--muted)">Comprehensive, high-quality care from cosmetic enhancements to<br>emergency treatments—tailored to your smile.</p>

  <div class="service-card" style="left:141px;top:156px">
    <div class="svc-icon"><svg viewBox="0 0 26 26" fill="none" stroke="#fff" stroke-width="1.6"><circle cx="13" cy="13" r="10"/><path d="M8.5 15c1.2 2 2.7 3 4.5 3s3.3-1 4.5-3"/><circle cx="9.5" cy="10.5" r=".8" fill="#fff"/><circle cx="16.5" cy="10.5" r=".8" fill="#fff"/></svg></div>
    <h3>Cosmetic Dentistry</h3>
    <p>Enhance your smile with treatments that improve tooth shape, color, and appearance.</p>
  </div>
  <div class="service-card" style="left:455px;top:156px">
    <div class="svc-icon"><svg viewBox="0 0 26 26" fill="none" stroke="#fff" stroke-width="1.6"><path d="M8 4c2 0 3 1 5 1s3-1 5-1c2 0 3 2 3 4 0 3-2 4-2 7l-1 7h-2l-1-5h-2l-1 5H10l-1-7c0-3-2-4-2-7 0-2 1-4 1-4z"/></svg></div>
    <h3>Dental Implants</h3>
    <p>Permanent, natural-looking tooth replacements that restore function and confidence.</p>
  </div>
  <div class="service-card" style="left:767px;top:156px">
    <div class="svc-icon"><svg viewBox="0 0 26 26" fill="none" stroke="#fff" stroke-width="1.6"><path d="M6 6l14 14M20 6L6 20"/><circle cx="6" cy="6" r="2"/><circle cx="20" cy="6" r="2"/></svg></div>
    <h3>Emergency Services</h3>
    <p>Quick, professional treatment for dental emergencies, providing relief when you need it most.</p>
  </div>
  <div class="service-card" style="left:141px;top:366px">
    <div class="svc-icon"><svg viewBox="0 0 26 26" fill="none" stroke="#fff" stroke-width="1.6"><path d="M4 10c3-2 15-2 18 0-1 6-5 9-9 9s-8-3-9-9z"/><path d="M7 11.5h12M10 11v4M13 11v5M16 11v4"/></svg></div>
    <h3>Teeth Whitening</h3>
    <p>Brighten your smile with safe, professional whitening treatments that deliver fast, noticeable results.</p>
  </div>
  <div class="service-card" style="left:455px;top:366px">
    <div class="svc-icon"><svg viewBox="0 0 26 26" fill="none" stroke="#fff" stroke-width="1.6"><path d="M7 5c2 0 3 1 5 1s3-1 5-1c2 0 3 2 3 4 0 3-2 4-2 7l-1 6h-2l-1-5h-2l-1 5H9l-1-6c0-3-2-4-2-7 0-2 1-4 1-4z"/><path d="M20 3v4M18 5h4"/></svg></div>
    <h3>Dental Hygiene</h3>
    <p>Preventive cleanings and exams to keep your teeth and gums healthy, fresh, and cavity-free.</p>
  </div>
  <div class="service-card" style="left:767px;top:366px">
    <div class="svc-icon"><svg viewBox="0 0 26 26" fill="none" stroke="#fff" stroke-width="1.6"><path d="M7 5c2 0 3 1 5 1s3-1 5-1c2 0 3 2 3 4 0 3-2 4-2 7l-1 6h-2l-1-5h-2l-1 5H9l-1-6c0-3-2-4-2-7 0-2 1-4 1-4z"/><path d="M10 9c1 2 3 2 4 0"/></svg></div>
    <h3>Tooth Restoration</h3>
    <p>Repair and restore damaged teeth with natural-looking fillings, crowns, and bridges for a healthier smile.</p>
  </div>
</section>

<section class="why">
  <h2 class="sec-title" style="top:57px">Why <span>Choose</span> Us?</h2>
  <p class="sec-sub" style="top:100px;left:400px;width:400px;color:#e6ebef">Experience expert care in a modern, comfort-first clinic—where<br>advanced technology meets personalized treatment.</p>

  <div class="why-item" style="top:186px">
    <div class="why-icon"><svg viewBox="0 0 38 38" fill="none" stroke="var(--teal)" stroke-width="2"><rect x="4" y="8" width="30" height="22" rx="2"/><rect x="9" y="12" width="20" height="14" rx="1"/><path d="M15 15c1.5 0 2.5.6 4 .6s2.5-.6 4-.6c.5 2-1 3-1 6h-2l-1-2-1 2h-2c0-3-1.5-4-1-6z" fill="var(--teal)"/></svg></div>
    <h3>Board-Certified Dentists</h3>
    <p>Expertise you can trust, backed by advanced training and credentials.</p>
  </div>
  <div class="why-item" style="top:300px">
    <div class="why-icon"><svg viewBox="0 0 38 38" fill="var(--teal)"><path d="M12 8c3 0 4 1.5 7 1.5S23 8 26 8c3 0 4 3 4 6 0 4-3 5-3 10l-1.5 9H23l-1.5-8h-5L15 33h-2.5L11 24c0-5-3-6-3-10 0-3 1-6 4-6z"/></svg></div>
    <h3>Pain-Free Treatments</h3>
    <p>Gentle techniques and modern technology for a stress-free experience.</p>
  </div>
  <div class="why-item" style="top:413px">
    <div class="why-icon"><svg viewBox="0 0 38 38" fill="none" stroke="var(--teal)" stroke-width="2"><path d="M8 24l10 2 8-6 4 2M18 26v6M12 32h12M10 10c4 0 6 3 6 6"/><circle cx="10" cy="10" r="3"/></svg></div>
    <h3>Luxury, Comfort-First Clinic</h3>
    <p>Designed to help you relax—because your comfort matters.</p>
  </div>
  <div class="why-item" style="top:525px">
    <div class="why-icon"><svg viewBox="0 0 38 38" fill="var(--teal)"><path d="M7 13h22a3 3 0 013 3v13a3 3 0 01-3 3H7a3 3 0 01-3-3V16a3 3 0 013-3z"/><path d="M8 12l16-6 3 6z"/><rect x="23" y="19" width="9" height="6" rx="2" fill="#e6ecee"/></svg></div>
    <h3>Flexible Payment Plans</h3>
    <p>Quality care made accessible with tailored financing options.</p>
  </div>

  <div class="why-frame"></div>
  <div class="why-photo" role="img" aria-label="Smiling dentist in a white coat with arms crossed in the clinic"></div>
</section>

<section class="visit">
  <h2 class="sec-title" style="top:75px;color:var(--navy)">Visit Our <span>Clinic</span></h2>
  <p class="sec-sub" style="top:117px;left:380px;width:440px;color:var(--muted)">Located in the heart of Brookhaven, our clinic offers flexible hours and easy<br>access to premium dental care.</p>

  <div class="map" role="img" aria-label="Street map showing the clinic location in the city"></div>

  <div class="info-card">
    <h4 style="top:30px"><svg viewBox="0 0 18 18" fill="none" stroke="var(--teal)" stroke-width="1.5"><path d="M9 16s5-5 5-9A5 5 0 004 7c0 4 5 9 5 9z"/><circle cx="9" cy="7" r="1.8"/></svg>Visit Us</h4>
    <p style="top:63px;left:37px">48 Willowmere Lane, Brookhaven</p>
    <h4 style="top:99px"><svg viewBox="0 0 18 18" fill="none" stroke="var(--teal)" stroke-width="1.5"><circle cx="9" cy="9" r="7"/><path d="M9 5v4l3 2"/></svg>Operating Hours</h4>
    <p style="top:134px">Mon–Fri: 8:00 AM – 6:00 PM<br>Sat: 9:00 AM – 2:00 PM<br>Closed Sundays</p>
    <h4 style="top:199px"><svg viewBox="0 0 18 18" fill="none" stroke="var(--teal)" stroke-width="1.5"><path d="M4 2.5l3 .5 1 3-2 1.5a9 9 0 004.5 4.5L12 10l3 1 .5 3-2 1.5C8 15 3 10 2.5 4.5z"/></svg>Call Us</h4>
    <p style="top:232px">(555) 014-2368</p>
    <div class="btn-call">Call Now</div>
  </div>
</section>

<section class="reviews">
  <h2 class="sec-title" style="top:60px">What Our Patients <span>Say</span></h2>
  <p class="sec-sub" style="top:103px;left:400px;width:400px;color:#e6ebef">Real stories from patients who've experienced compassionate care,<br>outstanding results, and a confident new smile.</p>

  <div class="arrow-btn" style="left:91px;border:1.5px solid #fff">
    <svg width="12" height="14" viewBox="0 0 12 14" fill="none" stroke="#fff" stroke-width="1.6"><path d="M8 1L2 7l6 6"/></svg>
  </div>
  <div class="arrow-btn" style="left:1080px;background:#fff">
    <svg width="12" height="14" viewBox="0 0 12 14" fill="none" stroke="var(--ink)" stroke-width="1.6"><path d="M4 1l6 6-6 6"/></svg>
  </div>

  <div class="review-card" style="left:141px">
    <div class="stars">
      <svg viewBox="0 0 20 20"><path d="M10 1l2.7 5.8 6.3.7-4.7 4.3 1.3 6.2L10 14.9 4.4 18l1.3-6.2L1 7.5l6.3-.7z" fill="var(--gold)"/></svg>
      <svg viewBox="0 0 20 20"><path d="M10 1l2.7 5.8 6.3.7-4.7 4.3 1.3 6.2L10 14.9 4.4 18l1.3-6.2L1 7.5l6.3-.7z" fill="var(--gold)"/></svg>
      <svg viewBox="0 0 20 20"><path d="M10 1l2.7 5.8 6.3.7-4.7 4.3 1.3 6.2L10 14.9 4.4 18l1.3-6.2L1 7.5l6.3-.7z" fill="var(--gold)"/></svg>
      <svg viewBox="0 0 20 20"><path d="M10 1l2.7 5.8 6.3.7-4.7 4.3 1.3 6.2L10 14.9 4.4 18l1.3-6.2L1 7.5l6.3-.7z" fill="var(--gold)"/></svg>
      <svg viewBox="0 0 20 20"><path d="M10 1l2.7 5.8 6.3.7-4.7 4.3 1.3 6.2L10 14.9 4.4 18l1.3-6.2L1 7.5l6.3-.7z" fill="var(--gold)"/></svg>
    </div>
    <div class="review-date">10th Feb, 2023</div>
    <p class="review-text">"The team made me feel comfortable from the moment I walked in. My<br>smile has never looked better!"</p>
    <div class="reviewer"><span class="reviewer-avatar" role="img" aria-label="Patient portrait"></span><div><b>Daniel R.</b><small>Customer</small></div></div>
  </div>

  <div class="review-card" style="left:611px">
    <div class="stars">
      <svg viewBox="0 0 20 20"><path d="M10 1l2.7 5.8 6.3.7-4.7 4.3 1.3 6.2L10 14.9 4.4 18l1.3-6.2L1 7.5l6.3-.7z" fill="var(--gold)"/></svg>
      <svg viewBox="0 0 20 20"><path d="M10 1l2.7 5.8 6.3.7-4.7 4.3 1.3 6.2L10 14.9 4.4 18l1.3-6.2L1 7.5l6.3-.7z" fill="var(--gold)"/></svg>
      <svg viewBox="0 0 20 20"><path d="M10 1l2.7 5.8 6.3.7-4.7 4.3 1.3 6.2L10 14.9 4.4 18l1.3-6.2L1 7.5l6.3-.7z" fill="var(--gold)"/></svg>
      <svg viewBox="0 0 20 20"><path d="M10 1l2.7 5.8 6.3.7-4.7 4.3 1.3 6.2L10 14.9 4.4 18l1.3-6.2L1 7.5l6.3-.7z" fill="var(--gold)"/></svg>
      <svg viewBox="0 0 20 20"><path d="M10 1l2.7 5.8 6.3.7-4.7 4.3 1.3 6.2L10 14.9 4.4 18l1.3-6.2L1 7.5l6.3-.7z" fill="var(--gold)"/></svg>
    </div>
    <div class="review-date">06th Feb, 2023</div>
    <p class="review-text">"Beautiful clinic, friendly staff, and pain-free treatment. Truly a premium<br>dental experience."</p>
    <div class="reviewer"><span class="reviewer-avatar" style="background:#d9b48c" role="img" aria-label="Patient portrait"></span><div><b>Clara W.</b><small>Customer</small></div></div>
  </div>

  <div class="btn-view">View All</div>
</section>

<footer class="site-footer">
  <div class="footer-brand">Harrowfield Dentistry</div>
  <nav class="footer-links"><span>Home</span><span>Our Services</span><span>Contact Us</span></nav>
  <div class="socials"><span></span><span></span><span></span></div>
  <div class="footer-rule"></div>
  <p class="copyright">© 2025 Harrowfield dentistry. All Rights Reserved.</p>
</footer>

</body>
</html>
```